Realty Group Needs Classy, Contemporary Letterhead Design

We need a letterhead design for a new realty company located in NY, USA. We buy investment properties to rehabilitate and or keep in our rental portfolio.

```html
<!DOCTYPE html>
<html lang="en">
<head>
<meta charset="utf-8">
<title>Halvorsen Realty Group – Letterhead</title>
<link rel="stylesheet" href="https://fonts.googleapis.com/css2?family=Open+Sans:wght@400;600;700&family=Lato:wght@400&display=swap">
<style>
  :root {
    --brand-purple: #4b2a8a;
    --ink: #4a4a4a;
    --ink-dark: #333333;
    --rule: #bdbdbd;
    --paper: #ffffff;
    --backdrop: #e4e4e6;
  }
  * { box-sizing: border-box; margin: 0; padding: 0; }
  html, body {
    width: 1040px; height: 1200px; overflow: hidden;
    background: var(--backdrop);
  }
  .letterhead {
    position: absolute; left: 53px; top: 0;
    width: 933px; height: 1200px;
    background: var(--paper);
    font-family: "Open Sans", Arial, sans-serif;
    color: var(--ink);
  }
  .brand {
    position: absolute; top: 42px; left: 0; width: 100%;
    display: flex; justify-content: center; align-items: center; gap: 10px;
  }
  .brand-dot {
    width: 16px; height: 16px; border-radius: 50%;
    background: var(--brand-purple);
  }
  .brand-name {
    font-weight: 700; font-size: 30px; letter-spacing: -0.5px;
    color: var(--brand-purple);
  }
  .block { position: absolute; left: 88px; width: 754px; font-size: 14.6px; }
  .issue-date { top: 216px; }
  .recipient { top: 253px; line-height: 18px; }
  .salutation { top: 356px; }
  .body-copy p {
    text-align: justify; line-height: 26.8px;
  }
  .para-1 { top: 408px; }
  .para-2 { top: 569px; }
  .para-3 { top: 676px; }
  .closing { top: 812px; }
  .signature {
    position: absolute; left: 88px; top: 852px;
    width: 214px; height: 24px;
    background: linear-gradient(90deg, rgba(70,70,70,0.35), rgba(70,70,70,0.15));
    border-radius: 12px;
  }
  .signer-name {
    top: 890px; font-size: 18.5px; font-weight: 600; color: var(--ink-dark);
  }
  .signer-title { top: 920px; }
  .footer-address {
    position: absolute; top: 1115px; left: 0; width: 100%;
    text-align: center; font-family: "Lato", Arial, sans-serif;
    font-size: 17.5px; color: #222;
  }
  .footer-rule {
    position: absolute; top: 1143px; left: 183px; width: 567px;
    border-top: 1px solid var(--rule);
  }
  .footer-contacts {
    position: absolute; top: 1149px; left: 0; width: 100%;
    display: flex; justify-content: center; gap: 10px;
    font-family: "Lato", Arial, sans-serif; font-size: 17.5px; color: #222;
  }
  .contact-item { display: flex; align-items: center; gap: 5px; }
  .contact-item svg { width: 22px; height: 22px; }
  .contact-web { margin-left: 6px; gap: 10px; }
  .base-band {
    position: absolute; left: 0; bottom: 0; width: 100%; height: 20px;
    background: var(--brand-purple);
  }
</style>
</head>
<body>
<main class="letterhead">
  <header class="brand">
    <span class="brand-dot"></span>
    <span class="brand-name">HALVORSEN Realty Group, LLC</span>
  </header>

  <p class="block issue-date">Issuing Date: May 5, 2018</p>
  <p class="block recipient">Name Of Employee Mr. XYZABC<br>Address of Employee<br>Address Line 2 etc..</p>
  <p class="block salutation">Dear Mr.XYZABC</p>

  <div class="body-copy">
    <p class="block para-1">Lorem Ipsum has been the industry's standard dummy text ever since the 1500s, when an unknown printer took a galley of type and scrambled it to make a type specimen book. It has survived not only five centuries, but also the leap into electronic typesetting, remaining essentially unchanged. It was popularised in the 1960s with the release of Typeline sheets containing Lorem Ipsum passages, and more recently with desktop publishing software like Norde PageForge including versions of Lorem Ipsum.</p>
    <p class="block para-2">Lorem Ipsum is simply dummy text of the printing and typesetting industry. Lorem Ipsum has been the industry's standard dummy text ever since the 1500s, when an unknown printer took a galley of type and scrambled it to make a type specimen book.</p>
    <p class="block para-3">It has survived not only five centuries, but also the leap into electronic typesetting, remaining essentially unchanged. It was popularised in the 1960s with the release of Typeline sheets containing Lorem IpsumIpsum passages.</p>
  </div>

  <p class="block closing">Yours Sincerely</p>
  <div class="signature" role="img" aria-label="Handwritten signature of Marcus Whitfield"></div>
  <p class="block signer-name">Marcus Whitfield</p>
  <p class="block signer-title">Managing Director</p>

  <footer>
    <p class="footer-address">218 Harlow Street, Albany NY, 12207</p>
    <div class="footer-rule"></div>
    <div class="footer-contacts">
      <span class="contact-item">
        <svg viewBox="0 0 22 22" aria-hidden="true"><circle cx="11" cy="11" r="10" fill="#4b2a8a"/><path d="M7.5 6.2l1.8-.4 1.1 2.6-1.2 1a6 6 0 0 0 3.3 3.3l1-1.2 2.6 1.1-.4 1.8c-4.4.4-8.6-3.8-8.2-8.2z" fill="#fff"/></svg>
        044-555 201 734
      </span>
      <span class="contact-item">
        <svg viewBox="0 0 22 22" aria-hidden="true"><circle cx="11" cy="11" r="10" fill="#4b2a8a"/><rect x="6" y="7.5" width="10" height="7" fill="#fff"/><path d="M6 7.5l5 4 5-4" fill="none" stroke="#4b2a8a" stroke-width="1"/></svg>
        info@halvorsenrg.com
      </span>
      <span class="contact-item contact-web">
        <svg viewBox="0 0 22 22" aria-hidden="true"><circle cx="11" cy="11" r="10" fill="#4b2a8a"/><circle cx="11" cy="11" r="5" fill="none" stroke="#fff" stroke-width="1.6"/><path d="M6 11h10M11 6c-2 3-2 7 0 10M11 6c2 3 2 7 0 10" fill="none" stroke="#fff" stroke-width="1"/></svg>
        www.halvorsenrg.com
      </span>
    </div>
    <div class="base-band"></div>
  </footer>
</main>
</body>
</html>
```